Stationery Set for Velmora Company

I need to create full stationery design for my company; Business Cards, Envelops, Letter Heads, Calendar.
In the letter head and Envelops... only contact information and website links.
Our company is a Service Management company with different domains of innovative services including Technology Service Management, Education Services, Outsourcing Management, Events Management.
I need a modern and innovative design specially for the business card. I some transparent designs and I like it, but don't limit your innovation to what I mentioned. Sky is limit for your innovation.

Target Market(s)

Middle East & Africa

Industry/Entity Type

Business Management

Colors
34a7d8
0355a3
85acd3
86cae7
cee9f5
cfdeed
e4daeb
f3f1f8
ecf7fb

Requirements
Must have
• Name, Title, Email, Mobile
Nice to have
• We have multiple locations in USA, KSA, EGY, so I need ideas about how to include all contact details maybe QR / Barcode or something else.
• Please see our locations and contact information: www.brightvelmora.example
Should not have
• Too much text

```html
<!DOCTYPE html>
<html lang="en">
<head>
<meta charset="utf-8">
<title>Velmora Company – Window Envelope</title>
<link rel="stylesheet" href="https://fonts.googleapis.com/css2?family=Questrial&display=swap">
<style>
  :root {
    --page-bg: #ffffff;
    --gold-deep: #b89a58;
    --gold-mid: #c2a35f;
    --gold-light: #dcbb6e;
    --ink-white: #ffffff;
    --band-light: #f4f4f4;
    --band-shade: #d9d9d9;
    --window-fill: #ffffff;
    --window-edge: #8a8a8a;
    --window-text: #8c8c8c;
  }
  * { margin: 0; padding: 0; box-sizing: border-box; }
  html, body {
    width: 1200px;
    height: 1000px;
    overflow: hidden;
    background: var(--page-bg);
  }
  .canvas {
    position: relative;
    width: 1200px;
    height: 1000px;
  }
  .envelope {
    position: absolute;
    left: 25px;
    top: 92px;
    width: 1145px;
    height: 818px;
    overflow: hidden;
    background:
      linear-gradient(90deg,
        var(--gold-deep) 0%,
        var(--gold-mid) 12%,
        var(--gold-deep) 20%,
        var(--gold-mid) 32%,
        var(--gold-light) 44%,
        var(--gold-mid) 52%,
        var(--gold-deep) 60%,
        var(--gold-light) 70%,
        var(--gold-mid) 78%,
        var(--gold-deep) 86%,
        var(--gold-light) 93%,
        var(--gold-mid) 100%);
    box-shadow: -4px 6px 8px rgba(0,0,0,0.35);
  }
  .ornament-area {
    position: absolute;
    left: 0;
    top: 55px;
    width: 520px;
    height: 295px;
    background: linear-gradient(100deg, rgba(255,255,255,0.14) 0%, rgba(255,255,255,0.07) 60%, rgba(255,255,255,0) 100%);
  }
  .sender {
    color: var(--ink-white);
    font-family: "Questrial", sans-serif;
  }
  .sender__name {
    position: absolute;
    left: 67px;
    top: 96px;
    font-size: 54px;
    line-height: 60px;
    letter-spacing: 0.5px;
    display: flex;
    align-items: center;
    gap: 14px;
  }
  .sender__mark {
    width: 18px;
    height: 18px;
    border-radius: 50%;
    background: var(--ink-white);
  }
  .sender__address {
    position: absolute;
    left: 69px;
    top: 242px;
    font-size: 21px;
    line-height: 32px;
    font-style: normal;
    white-space: nowrap;
  }
  .address-band {
    position: absolute;
    left: 0;
    top: 676px;
    width: 100%;
    height: 37px;
    background: linear-gradient(90deg, var(--band-light) 0%, var(--band-shade) 45%, var(--band-light) 75%, var(--band-light) 100%);
  }
  .window {
    position: absolute;
    left: 682px;
    top: 565px;
    width: 411px;
    height: 173px;
    background: var(--window-fill);
    border: 1px solid var(--window-edge);
    border-radius: 10px;
    padding: 39px 0 0 87px;
    font-family: Arial, Helvetica, sans-serif;
    font-size: 40px;
    line-height: 48px;
    color: var(--window-text);
  }
</style>
</head>
<body>
  <main class="canvas">
    <section class="envelope">
      <div class="ornament-area" role="img" aria-label="Area for a faint decorative line pattern behind the company name"></div>

      <header class="sender">
        <div class="sender__name"><span>Velmora</span><span class="sender__mark"></span></div>
        <address class="sender__address">
          418 Harbor Crest Road, 6th<br>
          Floor Lakemont CA 90417<br>
          US
        </address>
      </header>

      <div class="address-band"></div>

      <div class="window">WINDOW<br>(area to cut)</div>
    </section>
  </main>
</body>
</html>
```